Kelvo bottle Label (Yoghurt drink)

Label for a 300 ml yoghurt drink bottle in 3 flavours.

General description:
• This is to design a sleeve shrink label for a Yoghurt Drink bottle in three flavours, Classic, Strawberry and Blueberry.
• Attached 3 photos: The one with KELVO brand in the current design we want to replace using the same bottle.
• Graphically, the design is to be similar to the examples provided for drumelo and fizzcrate.
• Use font and barcode size to be readable and legal.
• Minimize the use of the upper third of the bottle as it will be distorted when the label shrinks to the bottle.
• Professional and experienced designers only are welcome, please do not waste your time otherwise.

Bottle dimensions:
• Base across: 61 mm
• Height: 145 mm (approximate)

Graphical description:
• White colour with bands at the top and bottom similar to the one in “drumelo” example provided (not necessarily identical, feel free to be creative.
• The upper and lower bands to be: Green for “classic”, Pink or red for strawberry and purple for blueberry flavour.
• On the front: the brand name “Kelvo” and description “Yoghurt Drink” to be graphically attractive.
• On the front: two or more pieces of strawberry or blueberry for each flavour placed nicely with the option to include “yoghurt splash” or any suitable affects you deem suitable.
• For the Classic flavour, use the words (Classic, Lassi, Ayran) in the same location for the berries done in a graphically suitable manner.
• Colour temperature for the three flavours to be similar.

Information and objects on the label:
Front:
• The word “Kelvo” (brand name)
• “Yoghurt drink” (Product description)
• “300 ml” (size)
• Picture of Strawberries for strawberry flavour.
• Picture of Blueberries for blueberry flavour.
• The words (Classic, Lassi, Ayran) in the place used for the strawberries in the flavoured type, distributed to look graphically suitable for the overall design.

Back:
• Ingredient: Milk/milk solids, culture, salt, water, sugar, colour, flavour. (this is to be finalized later)
• Nutrition information table: (to be provided later).
• Barcode (to be provided later)
• Product of Australia
• Morel Tunsley Pty Ltd, 5/14 Ferrit St, Malaga, WA 6090
• info@kelvo-example.com.au 0491 000 372
• Keep under 5⁰ C
• Best before date printed on the bottle
• Shake well (to be located on the side at the top)
• Recycle icon.

Health benefits: (to be located suitably, possibly on the side with vertical orientation)
• Rich in probiotic bacteria and vitamins.
• Improves digestion and bowel motion.
• Supports weight control and fat loss.

Target Market(s)

General consumers

Industry/Entity Type

Grocery Store

Font styles to use
Sans Serif

Colors
abd037
b768aa
f04a50

Requirements
Must have
• The details in the project description
• The design must be simple and neat.
• Please use the shape of the current bottle "Kelvo" as in the attached photo.
Should not have
• Busy, cluttered, or empty and incomplete designs.

```html
<!DOCTYPE html>
<html lang="en">
<head>
<meta charset="utf-8">
<title>Kelvo Yoghurt Drink – Strawberry Label</title>
<link href="https://fonts.googleapis.com/css2?family=Roboto+Condensed:wght@400;700&family=Archivo:wght@300;800&display=swap" rel="stylesheet">
<style>
  :root {
    --band-red: #c8252d;
    --band-red-light: #e06a6f;
    --accent-pink: #d85d68;
    --line-pink: #e0707a;
    --line-grey: #d6d6d6;
    --text-red: #c41e24;
    --text-grey: #8a8a8a;
    --label-white: #f7f7f7;
    --label-shade: #e9e9e9;
  }
  * { margin: 0; padding: 0; box-sizing: border-box; }
  html, body { width: 1200px; height: 2848px; overflow: hidden; background: #ffffff; }
  .label {
    position: relative;
    width: 1200px;
    height: 2848px;
    overflow: hidden;
    background: linear-gradient(135deg, #ffffff 0%, var(--label-white) 55%, var(--label-shade) 100%);
    font-family: "Roboto Condensed", "Arial Narrow", sans-serif;
  }
  .band-top {
    position: absolute; left: 0; top: 0; width: 100%; height: 100px;
    background: linear-gradient(180deg, var(--band-red) 0%, var(--band-red-light) 100%);
  }
  .rule-top {
    position: absolute; left: 0; top: 100px; width: 100%; height: 18px;
    background: var(--line-grey);
  }
  .rule-bottom-pink {
    position: absolute; left: 0; top: 2566px; width: 100%; height: 22px;
    background: var(--line-pink);
  }
  .rule-bottom-grey {
    position: absolute; left: 0; top: 2588px; width: 100%; height: 20px;
    background: var(--line-grey);
  }
  .band-bottom {
    position: absolute; left: 0; top: 2610px; width: 100%; height: 238px;
    background: linear-gradient(180deg, var(--band-red-light) 0%, var(--band-red) 45%, var(--band-red) 100%);
  }
  .emblem { position: absolute; left: 0; top: 0; width: 1200px; height: 2848px; }
  .flavour-name {
    position: absolute; right: 155px; top: 1488px;
    font-size: 104px; font-weight: 400; color: var(--text-red); line-height: 1;
  }
  .flavour-word {
    position: absolute; right: 155px; top: 1640px;
    font-size: 70px; font-weight: 400; color: var(--text-grey); line-height: 1;
  }
  .brand-name {
    position: absolute; left: 0; width: 100%; top: 1900px;
    text-align: center; font-size: 418px; font-weight: 700;
    color: var(--accent-pink); line-height: 1; letter-spacing: 6px;
  }
  .product-type {
    position: absolute; left: 0; width: 100%; top: 2340px;
    text-align: center; font-family: "Archivo", Arial, sans-serif;
    font-size: 92px; color: var(--text-grey); line-height: 1; letter-spacing: 1px;
  }
  .product-type .light { font-weight: 300; }
  .product-type .bold { font-weight: 800; }
  .claim, .volume {
    position: absolute; top: 2718px; font-size: 58px; color: #ffffff; line-height: 1;
  }
  .claim { left: 42px; }
  .volume { right: 60px; }
</style>
</head>
<body>
<div class="label">
  <div class="band-top"></div>
  <div class="rule-top"></div>

  <svg class="emblem" viewBox="0 0 632 1500" preserveAspectRatio="none" xmlns="http://www.w3.org/2000/svg">
    <defs>
      <filter id="soft-shadow" x="-20%" y="-20%" width="140%" height="140%">
        <feDropShadow dx="6" dy="10" stdDeviation="10" flood-color="#000" flood-opacity="0.18"/>
      </filter>
      <radialGradient id="berry-fill" cx="50%" cy="45%" r="60%">
        <stop offset="0%" stop-color="#e23a35"/>
        <stop offset="100%" stop-color="#a8121a"/>
      </radialGradient>
      <radialGradient id="peak-fill" cx="50%" cy="50%" r="60%">
        <stop offset="0%" stop-color="#c9c9c9"/>
        <stop offset="100%" stop-color="#efefef"/>
      </radialGradient>
    </defs>

    <g class="emblem-frame" filter="url(#soft-shadow)" fill="#ebebeb">
      <circle cx="175" cy="230" r="130"/>
      <circle cx="405" cy="555" r="178"/>
      <path d="M255 330 C 300 360, 250 420, 262 470 L 300 440 C 290 400, 340 360, 290 260 Z"/>
      <path d="M80 320 C 160 360, 250 330, 300 420 L 420 400 C 330 260, 260 300, 260 180 Z"/>
    </g>
    <circle cx="177" cy="232" r="102" fill="#f8f8f8"/>
    <circle cx="400" cy="550" r="142" fill="#f8f8f8"/>
    <circle cx="177" cy="232" r="85" fill="none" stroke="#d95560" stroke-width="3"/>
    <circle cx="400" cy="550" r="118" fill="none" stroke="#d95560" stroke-width="3"/>

    <ellipse cx="180" cy="225" rx="60" ry="28" fill="url(#peak-fill)" role="img" aria-label="Mountain peaks emblem"/>
    <ellipse cx="400" cy="545" rx="100" ry="60" fill="url(#berry-fill)" role="img" aria-label="Two fresh strawberries"/>
  </svg>

  <div class="flavour-name">Strawberry</div>
  <div class="flavour-word">Flavour</div>

  <div class="brand-name">KELVO</div>
  <div class="product-type"><span class="light">YOGHURT </span><span class="bold">DRINK</span></div>

  <div class="rule-bottom-pink"></div>
  <div class="rule-bottom-grey"></div>
  <div class="band-bottom"></div>
  <div class="claim">100% Natural Ingredients</div>
  <div class="volume">300ml.</div>
</div>
</body>
</html>
```